Aquavelo- plumbing service flyer

Hello,
We would like to create flyer for our plumbing company Aquavelo
- we have 2 web domains
aquavelo-example.hr ( official)
preuredjenjedoma-example.hr ( for bathroom renovation)

- we would like to create a similar Z-fold flyer ( from A4 paper) for our services
- We are sending images used on our websites. Of Course, it is allowed to put some of their own. Depending on design
- sending word with text which should go on each page. Text can be modified but in the sense of a page. The massage on a page should be as in word.
What is important to us:
- to stay in blue color
- It should be 1 page when fully open. So it looks like the complete page of information
- first/front page should be with our logo and phone number. more focus on emergency plumbing.
- back page should be about bathroom remodeling. Not necessary but would be received more points
- please don't use images of regular plumbers from Pixelvault and similar. we don't want to use this stock's regular images as all others.

Target Market(s)

Bathroom remodeling and emergency plumbing

Industry/Entity Type

Construction-Plumbing

Colors
0054AA
0677BA
7BADD7
CADEEF
E8F1F8

Requirements
Must have
• Logo

```html
<!DOCTYPE html>
<html lang="en">
<head>
<meta charset="utf-8">
<title>Aquavelo – plumbing service flyer</title>
<link href="https://fonts.googleapis.com/css2?family=Bebas+Neue&family=Montserrat:wght@400;500;600;700&display=swap" rel="stylesheet">
<style>
:root{
  --navy:#0a2a78;
  --deep:#0054aa;
  --mid:#0677ba;
  --bright:#1a9be0;
  --sky:#7badd7;
  --pale:#cadeef;
  --mist:#e8f1f8;
  --gold:#f6b21a;
  --stage:#a7a9ac;
  --white:#ffffff;
}
*{box-sizing:border-box;margin:0;padding:0}
html,body{width:805px;height:1200px;overflow:hidden}
body{background:var(--stage);font-family:"Montserrat",sans-serif;color:var(--white);position:relative}
.sheet{position:absolute;left:76px;width:660px;height:468px;overflow:hidden;box-shadow:0 10px 14px rgba(0,0,0,.25)}
.sheet--outside{top:114px}
.sheet--inside{top:647px}
.panel{position:absolute;top:0;width:220px;height:468px;overflow:hidden}
.panel--a{left:0}.panel--b{left:220px}.panel--c{left:440px}
.bg-light{background:linear-gradient(160deg,#1fa7ea 0%,var(--mid) 70%,var(--deep) 100%)}
.bg-navy{background:linear-gradient(180deg,var(--deep) 0%,var(--navy) 100%)}
.abs{position:absolute;z-index:2}
.wordmark{font-family:"Montserrat",sans-serif;font-weight:700;color:var(--white);letter-spacing:1px;text-transform:uppercase}
.display{font-family:"Bebas Neue",sans-serif;letter-spacing:.3px;line-height:1}
.gold{color:var(--gold)}
.copy{font-size:8.4px;line-height:1.25}
.copy--bold{font-weight:600}
.faint{color:#5fb3e8;font-size:7.4px;line-height:1.3}
.pill{background:var(--gold);color:var(--white);font-family:"Bebas Neue",sans-serif;font-size:13px;line-height:1.1;padding:3px 12px;border-radius:0 12px 12px 0;white-space:nowrap}
.service-list{list-style:none}
.service-list li{display:flex;align-items:center;gap:8px;font-size:8.2px;line-height:1.15;height:20px}
.service-icon{flex:none;width:18px;height:18px;border-radius:50%;background:var(--white);border:2px solid var(--pale)}
.check-list{list-style:none}
.check-list li{display:flex;align-items:flex-start;gap:6px;font-size:8.4px;line-height:1.2;margin-bottom:4.7px}
.check-list svg{flex:none;margin-top:1px}
.step-list{list-style:none}
.step-list li{display:flex;align-items:center;gap:10px;font-size:8.6px;height:22.7px;white-space:nowrap}
.phone{display:inline-flex;align-items:center;gap:3px;background:var(--gold);border-radius:12px;padding:0 10px 0 0;height:19px;font-weight:700;font-size:13px;color:var(--white);white-space:nowrap}
.phone-icon{width:21px;height:21px;border-radius:50%;background:var(--white);display:flex;align-items:center;justify-content:center;margin-left:-2px}
.url{font-size:9.4px;line-height:1.25;text-align:center;white-space:nowrap}
.url b{font-weight:600;color:#5fc0f5}
.art{position:absolute;z-index:1}
.badge{position:absolute;z-index:2;display:flex;flex-direction:column;align-items:center;justify-content:center;gap:4px}
.badge-disc{width:46px;height:46px;border-radius:50%;background:var(--white)}
.hex-row{display:flex;gap:8px}
.hex-row .tile{width:34px;text-align:center;font-size:5.6px;line-height:1.1;color:var(--white)}
.tile-shape{width:34px;height:34px;border-radius:50%;background:linear-gradient(180deg,#fff,var(--pale));margin-bottom:3px;border:2px solid #7bd0f5}
.center{text-align:center}
</style>
</head>
<body>

<section class="sheet sheet--outside">

  <div class="panel panel--a bg-light">
    <div class="abs wordmark" style="left:41px;top:20px;font-size:24px">Aquavelo</div>
    <p class="abs copy copy--bold" style="left:13px;top:63px;width:200px">Do you need a plumber for bathroom renovation? Did your pipe burst or have some clogging in pipes?<br>The neighbor's has ceiling leak?</p>
    <p class="abs faint" style="left:13px;top:112px;width:196px">We offer plumbing services in the area of the City of Zagreb and its surroundings.</p>
    <div class="abs pill" style="left:0;top:141px;width:165px">Plumbing services include:</div>
    <ul class="abs service-list" style="left:12px;top:168px;width:205px">
      <li><span class="service-icon"></span>Installation of new plumbing systems</li>
      <li><span class="service-icon"></span>Repair of leaking pipes, faucets, and fixtures</li>
      <li><span class="service-icon"></span>Drain cleaning and unclogging</li>
      <li><span class="service-icon"></span>Sewer line repair and replacement</li>
      <li><span class="service-icon"></span>Bathroom and kitchen plumbing installation and repair</li>
    </ul>
    <p class="abs display gold center" style="left:0;top:293px;width:220px;font-size:14px;line-height:1.1">Reliability, speed, accessibility.<br>Your Aquavelo.</p>
    <svg class="art" style="left:0;top:330px" width="220" height="138" viewBox="0 0 220 138" aria-hidden="true">
      <path d="M0 30 Q90 0 220 18 L220 138 L0 138Z" fill="var(--gold)"/>
      <path d="M0 38 Q90 8 220 26 L220 138 L0 138Z" fill="var(--navy)"/>
    </svg>
    <div class="art" role="img" aria-label="Superhero plumber mascot holding a pipe wrench over his shoulder, giving a thumbs up" style="left:62px;top:338px;width:150px;height:130px;border-radius:40% 40% 0 0;background:radial-gradient(circle at 50% 40%,#4fb6ee,#1f6fc0 70%)"></div>
  </div>

  <div class="panel panel--b bg-light">
    <div class="badge" style="left:50px;top:18px;width:120px;height:132px">
      <span class="badge-disc"></span>
      <span class="wordmark" style="font-size:20px">Aquavelo</span>
    </div>
    <h2 class="abs display center" style="left:0;top:172px;width:220px;font-size:20px;font-weight:400">Emergency plumbing</h2>
    <ul class="abs check-list" style="left:40px;top:201px;width:175px">
      <li><svg width="8" height="8" viewBox="0 0 10 10"><circle cx="5" cy="5" r="4" fill="none" stroke="var(--gold)" stroke-width="1.3"/><path d="M3 5l1.5 1.5L7 3.8" fill="none" stroke="var(--gold)" stroke-width="1.3"/></svg>Mechanical drain cleaning</li>
      <li><svg width="8" height="8" viewBox="0 0 10 10"><circle cx="5" cy="5" r="4" fill="none" stroke="var(--gold)" stroke-width="1.3"/><path d="M3 5l1.5 1.5L7 3.8" fill="none" stroke="var(--gold)" stroke-width="1.3"/></svg>Water jet pipe cleaning</li>
      <li><svg width="8" height="8" viewBox="0 0 10 10"><circle cx="5" cy="5" r="4" fill="none" stroke="var(--gold)" stroke-width="1.3"/><path d="M3 5l1.5 1.5L7 3.8" fill="none" stroke="var(--gold)" stroke-width="1.3"/></svg>Leak detections</li>
      <li><svg width="8" height="8" viewBox="0 0 10 10"><circle cx="5" cy="5" r="4" fill="none" stroke="var(--gold)" stroke-width="1.3"/><path d="M3 5l1.5 1.5L7 3.8" fill="none" stroke="var(--gold)" stroke-width="1.3"/></svg>Pipe inspection with camera</li>
      <li><svg width="8" height="8" viewBox="0 0 10 10"><circle cx="5" cy="5" r="4" fill="none" stroke="var(--gold)" stroke-width="1.3"/><path d="M3 5l1.5 1.5L7 3.8" fill="none" stroke="var(--gold)" stroke-width="1.3"/></svg>Thermal imaging of leakes</li>
      <li><svg width="8" height="8" viewBox="0 0 10 10"><circle cx="5" cy="5" r="4" fill="none" stroke="var(--gold)" stroke-width="1.3"/><path d="M3 5l1.5 1.5L7 3.8" fill="none" stroke="var(--gold)" stroke-width="1.3"/></svg>Main pipe check up</li>
      <li><svg width="8" height="8" viewBox="0 0 10 10"><circle cx="5" cy="5" r="4" fill="none" stroke="var(--gold)" stroke-width="1.3"/><path d="M3 5l1.5 1.5L7 3.8" fill="none" stroke="var(--gold)" stroke-width="1.3"/></svg>Valve change</li>
      <li><svg width="8" height="8" viewBox="0 0 10 10"><circle cx="5" cy="5" r="4" fill="none" stroke="var(--gold)" stroke-width="1.3"/><path d="M3 5l1.5 1.5L7 3.8" fill="none" stroke="var(--gold)" stroke-width="1.3"/></svg>Change of sink siphon</li>
    </ul>
    <p class="abs display center" style="left:0;top:328px;width:220px;font-size:11.5px;line-height:1.25">Aquavelo team will help you to<br>manage all the plumbing crises</p>
    <svg class="art" style="left:0;top:360px" width="220" height="108" viewBox="0 0 220 108" aria-hidden="true">
      <path d="M0 10 Q110 38 220 12 L220 108 L0 108Z" fill="var(--gold)"/>
      <path d="M0 14 Q110 42 220 16 L220 108 L0 108Z" fill="var(--navy)"/>
    </svg>
    <p class="abs display center" style="left:0;top:398px;width:220px;font-size:14px;color:#7bd0f5">Fast and reliable</p>
    <div class="abs" style="left:43px;top:419px"><span class="phone"><span class="phone-icon"><svg width="11" height="11" viewBox="0 0 24 24"><path d="M6.6 10.8a15 15 0 006.6 6.6l2.2-2.2a1 1 0 011-.25 11.4 11.4 0 003.6.57 1 1 0 011 1V20a1 1 0 01-1 1A17 17 0 013 4a1 1 0 011-1h3.5a1 1 0 011 1c0 1.25.2 2.45.57 3.6a1 1 0 01-.25 1z" fill="var(--mid)"/></svg></span>+385 91 000 4821</span></div>
    <p class="abs center" style="left:0;top:445px;width:220px;font-size:8.2px;font-weight:500">CONTACT US DAILY 24/7</p>
  </div>

  <div class="panel panel--c bg-light">
    <div class="abs wordmark center" style="left:0;top:34px;width:220px;font-size:30px">Aquavelo</div>
    <div class="abs hex-row" style="left:30px;top:92px">
      <div class="tile"><div class="tile-shape"></div>Bathroom Remodeling</div>
      <div class="tile"><div class="tile-shape"></div>Emergency Plumbing</div>
      <div class="tile"><div class="tile-shape"></div>Plumbing Repairs</div>
      <div class="tile"><div class="tile-shape"></div>Leak Detection</div>
    </div>
    <svg class="art" style="left:0;top:120px" width="220" height="348" viewBox="0 0 220 348" aria-hidden="true">
      <path d="M0 348 L0 110 Q120 80 220 0 L220 348Z" fill="var(--gold)"/>
      <path d="M0 348 L0 118 Q125 92 220 12 L220 348Z" fill="var(--bright)"/>
      <path d="M0 348 L0 132 Q130 110 220 36 L220 348Z" fill="var(--deep)"/>
    </svg>
    <div class="art" role="img" aria-label="Flying superhero plumber mascot in a blue suit with one fist raised" style="left:20px;top:180px;width:185px;height:215px;border-radius:50%;background:radial-gradient(circle at 50% 45%,#6cc4f2,#1f7dd0 75%)"></div>
    <div class="abs" style="left:30px;top:409px"><span class="phone"><span class="phone-icon"><svg width="11" height="11" viewBox="0 0 24 24"><path d="M6.6 10.8a15 15 0 006.6 6.6l2.2-2.2a1 1 0 011-.25 11.4 11.4 0 003.6.57 1 1 0 011 1V20a1 1 0 01-1 1A17 17 0 013 4a1 1 0 011-1h3.5a1 1 0 011 1c0 1.25.2 2.45.57 3.6a1 1 0 01-.25 1z" fill="var(--mid)"/></svg></span>+385 91 000 4821</span></div>
    <p class="abs url" style="left:0;top:434px;width:220px">www.<b>aquavelo-example</b>.hr<br>www.<b>preuredjenjedoma-example</b>.hr</p>
  </div>
</section>

<section class="sheet sheet--inside">

  <div class="panel panel--a bg-navy">
    <svg class="art" style="left:150px;top:0" width="70" height="468" viewBox="0 0 70 468" aria-hidden="true">
      <path d="M40 0 Q10 120 30 240 Q50 360 20 468 L70 468 L70 0Z" fill="var(--gold)"/>
      <path d="M48 0 Q18 120 38 240 Q58 360 28 468 L70 468 L70 0Z" fill="var(--mid)"/>
    </svg>
    <div class="badge" style="left:28px;top:28px;width:120px;height:135px">
      <span class="badge-disc"></span>
      <span class="wordmark" style="font-size:20px">Aquavelo</span>
    </div>
    <div class="art" role="img" aria-label="Illustration of grey water pipes with yellow and red valves" style="left:160px;top:178px;width:50px;height:185px;border-radius:24px;background:linear-gradient(180deg,#3d5a8a,#1d3f7a)"></div>
    <div class="abs pill" style="left:0;top:190px;width:112px;background:var(--mid);font-size:12.5px">Plumbing steps:</div>
    <ol class="abs step-list" style="left:18px;top:213px;width:150px">
      <li><svg width="20" height="20" viewBox="0 0 20 20"><path d="M10 1l8 4.5v9L10 19l-8-4.5v-9z" fill="none" stroke="var(--gold)" stroke-width="1"/><text x="10" y="13.5" font-size="9" text-anchor="middle" fill="#fff" font-family="Bebas Neue, sans-serif">1</text></svg>Planning faze</li>
      <li><svg width="20" height="20" viewBox="0 0 20 20"><path d="M10 1l8 4.5v9L10 19l-8-4.5v-9z" fill="none" stroke="var(--gold)" stroke-width="1"/><text x="10" y="13.5" font-size="9" text-anchor="middle" fill="#fff" font-family="Bebas Neue, sans-serif">2</text></svg>Demolition</li>
      <li><svg width="20" height="20" viewBox="0 0 20 20"><path d="M10 1l8 4.5v9L10 19l-8-4.5v-9z" fill="none" stroke="var(--gold)" stroke-width="1"/><text x="10" y="13.5" font-size="9" text-anchor="middle" fill="#fff" font-family="Bebas Neue, sans-serif">3</text></svg>Plumbing faze</li>
      <li><svg width="20" height="20" viewBox="0 0 20 20"><path d="M10 1l8 4.5v9L10 19l-8-4.5v-9z" fill="none" stroke="var(--gold)" stroke-width="1"/><text x="10" y="13.5" font-size="9" text-anchor="middle" fill="#fff" font-family="Bebas Neue, sans-serif">4</text></svg>Electric work</li>
      <li><svg width="20" height="20" viewBox="0 0 20 20"><path d="M10 1l8 4.5v9L10 19l-8-4.5v-9z" fill="none" stroke="var(--gold)" stroke-width="1"/><text x="10" y="13.5" font-size="9" text-anchor="middle" fill="#fff" font-family="Bebas Neue, sans-serif">5</text></svg>Ceramic work</li>
      <li><svg width="20" height="20" viewBox="0 0 20 20"><path d="M10 1l8 4.5v9L10 19l-8-4.5v-9z" fill="none" stroke="var(--gold)" stroke-width="1"/><text x="10" y="13.5" font-size="9" text-anchor="middle" fill="#fff" font-family="Bebas Neue, sans-serif">6</text></svg>Final sanitary installation</li>
      <li><svg width="20" height="20" viewBox="0 0 20 20"><path d="M10 1l8 4.5v9L10 19l-8-4.5v-9z" fill="none" stroke="var(--gold)" stroke-width="1"/><text x="10" y="13.5" font-size="9" text-anchor="middle" fill="#fff" font-family="Bebas Neue, sans-serif">7</text></svg>Final cleaning</li>
    </ol>
    <div class="abs" style="left:24px;top:393px"><span class="phone" style="font-size:14px"><span class="phone-icon"><svg width="11" height="11" viewBox="0 0 24 24"><path d="M6.6 10.8a15 15 0 006.6 6.6l2.2-2.2a1 1 0 011-.25 11.4 11.4 0 003.6.57 1 1 0 011 1V20a1 1 0 01-1 1A17 17 0 013 4a1 1 0 011-1h3.5a1 1 0 011 1c0 1.25.2 2.45.57 3.6a1 1 0 01-.25 1z" fill="var(--mid)"/></svg></span>+385 91 000 4821</span></div>
    <p class="abs url" style="left:6px;top:420px;width:186px;font-size:9.6px">www.<b>aquavelo-example</b>.hr<br>www.<b>preuredjenjedoma-example</b>.hr</p>
  </div>

  <div class="panel panel--b bg-light">
    <svg class="art" style="left:0;top:180px" width="220" height="288" viewBox="0 0 220 288" aria-hidden="true">
      <path d="M0 0 Q40 60 30 150 Q25 230 95 288 L0 288Z" fill="var(--deep)"/>
      <path d="M120 288 Q175 230 170 150 Q168 80 200 0 L220 0 L220 288Z" fill="var(--deep)"/>
      <path d="M108 288 Q160 230 156 160" fill="none" stroke="var(--gold)" stroke-width="5"/>
    </svg>
    <p class="abs display gold center" style="left:0;top:30px;width:220px;font-size:12.5px;line-height:1.25">What to check before installation<br>and putting tiles on walls</p>
    <ul class="abs check-list" style="left:22px;top:68px;width:195px">
      <li style="margin-bottom:9px"><svg width="8" height="8" viewBox="0 0 10 10"><circle cx="5" cy="5" r="4" fill="none" stroke="var(--gold)" stroke-width="1.3"/><path d="M3 5l1.5 1.5L7 3.8" fill="none" stroke="var(--gold)" stroke-width="1.3"/></svg><span>Decide on type of pipes:<br>PEX, PPR, inox</span></li>
      <li style="margin-bottom:9px"><svg width="8" height="8" viewBox="0 0 10 10"><circle cx="5" cy="5" r="4" fill="none" stroke="var(--gold)" stroke-width="1.3"/><path d="M3 5l1.5 1.5L7 3.8" fill="none" stroke="var(--gold)" stroke-width="1.3"/></svg><span>Inspect pipes with camera to check is pipe fall ok</span></li>
      <li style="margin-bottom:9px"><svg width="8" height="8" viewBox="0 0 10 10"><circle cx="5" cy="5" r="4" fill="none" stroke="var(--gold)" stroke-width="1.3"/><path d="M3 5l1.5 1.5L7 3.8" fill="none" stroke="var(--gold)" stroke-width="1.3"/></svg><span>Test water pipes with test pump</span></li>
      <li><svg width="8" height="8" viewBox="0 0 10 10"><circle cx="5" cy="5" r="4" fill="none" stroke="var(--gold)" stroke-width="1.3"/><path d="M3 5l1.5 1.5L7 3.8" fill="none" stroke="var(--gold)" stroke-width="1.3"/></svg><span>Take images of each wall with install pipes on it before closing</span></li>
    </ul>
    <div class="art" role="img" aria-label="Superhero plumber mascot standing inside a circle, holding a pipe" style="left:40px;top:198px;width:150px;height:200px;border-radius:50%;background:radial-gradient(circle at 50% 45%,#6cc4f2,#1a6fc4 75%);border:3px solid #fff"></div>
  </div>

  <div class="panel panel--c bg-light">
    <div class="abs pill" style="left:0;top:29px;font-size:12px;padding:3px 10px 3px 12px">Steps for renovating a bathroom:</div>
    <ol class="abs step-list" style="left:14px;top:60px;width:200px">
      <li><svg width="20" height="20" viewBox="0 0 20 20"><path d="M10 1l8 4.5v9L10 19l-8-4.5v-9z" fill="none" stroke="var(--gold)" stroke-width="1"/><text x="10" y="13.5" font-size="9" text-anchor="middle" fill="#fff" font-family="Bebas Neue, sans-serif">1</text></svg>Plan your budget</li>
      <li><svg width="20" height="20" viewBox="0 0 20 20"><path d="M10 1l8 4.5v9L10 19l-8-4.5v-9z" fill="none" stroke="var(--gold)" stroke-width="1"/><text x="10" y="13.5" font-size="9" text-anchor="middle" fill="#fff" font-family="Bebas Neue, sans-serif">2</text></svg>Plan your design</li>
      <li><svg width="20" height="20" viewBox="0 0 20 20"><path d="M10 1l8 4.5v9L10 19l-8-4.5v-9z" fill="none" stroke="var(--gold)" stroke-width="1"/><text x="10" y="13.5" font-size="9" text-anchor="middle" fill="#fff" font-family="Bebas Neue, sans-serif">3</text></svg>Hire a proffesionals</li>
      <li><svg width="20" height="20" viewBox="0 0 20 20"><path d="M10 1l8 4.5v9L10 19l-8-4.5v-9z" fill="none" stroke="var(--gold)" stroke-width="1"/><text x="10" y="13.5" font-size="9" text-anchor="middle" fill="#fff" font-family="Bebas Neue, sans-serif">4</text></svg>Decide about sanitary ware</li>
      <li><svg width="20" height="20" viewBox="0 0 20 20"><path d="M10 1l8 4.5v9L10 19l-8-4.5v-9z" fill="none" stroke="var(--gold)" stroke-width="1"/><text x="10" y="13.5" font-size="9" text-anchor="middle" fill="#fff" font-family="Bebas Neue, sans-serif">5</text></svg>Choose tile and paint</li>
      <li><svg width="20" height="20" viewBox="0 0 20 20"><path d="M10 1l8 4.5v9L10 19l-8-4.5v-9z" fill="none" stroke="var(--gold)" stroke-width="1"/><text x="10" y="13.5" font-size="9" text-anchor="middle" fill="#fff" font-family="Bebas Neue, sans-serif">6</text></svg>Install bathroom accessories</li>
      <li><svg width="20" height="20" viewBox="0 0 20 20"><path d="M10 1l8 4.5v9L10 19l-8-4.5v-9z" fill="none" stroke="var(--gold)" stroke-width="1"/><text x="10" y="13.5" font-size="9" text-anchor="middle" fill="#fff" font-family="Bebas Neue, sans-serif">7</text></svg>Clean up</li>
    </ol>
    <p class="abs center" style="left:10px;top:236px;width:200px;font-size:8.6px;line-height:1.35">By following these steps, you can successfully renovate your bathroom and create a space that meets your needs and style preferences.</p>
    <div class="art" role="img" aria-label="Round photo of a copper faucet over a sink" style="left:15px;top:306px;width:62px;height:62px;border-radius:50%;background:radial-gradient(circle,#8a7a6a,#3f4a5a);border:2px solid #fff"></div>
    <div class="art" role="img" aria-label="Round photo of hands fitting pipes under a sink" style="left:72px;top:297px;width:72px;height:72px;border-radius:50%;background:radial-gradient(circle,#7f8a96,#2c3a4e);border:2px solid #fff"></div>
    <div class="art" role="img" aria-label="Round photo of a bright tiled shower with a chrome shower head" style="left:139px;top:306px;width:62px;height:62px;border-radius:50%;background:radial-gradient(circle,#d9e7f1,#8fb2cc);border:2px solid #fff"></div>
    <p class="abs center" style="left:10px;top:411px;width:200px;font-size:7.6px;line-height:1.3;color:var(--pale)">This steps will help you to be sure that installations are ok before closing.</p>
  </div>
</section>

</body>
</html>
```